Update patient consent forms and contract

Objective
Redesign the existing patient contract information document to create a modern,contempory, and easy-to-understand experience for patients. The updated design should improve readability, accessibility, and overall presentation while maintaining compliance with healthcare and legal requirements.

Key Deliverables

Refreshed visual design and layout
Improved information hierarchy and readability
Modern typography and colour palette aligned with brand guidelines
Clear section headings and navigation
Print-ready and digital versions (PDF)

Include KEV Logo within patient KEV consent to treatment. Ideally this document should be portrait not landscape.
Updates

I would love a front page to be included in the document

```html
<!DOCTYPE html>
<html lang="en">
<head>
<meta charset="utf-8">
<title>KEV Patient Consent Form</title>
<link href="https://fonts.googleapis.com/css2?family=Montserrat:wght@300;400;500;700&display=swap" rel="stylesheet">
<style>
:root{
  --navy:#1b2443;
  --ink:#4d4d4f;
  --rule:#1b2443;
  --paper:#ffffff;
  --frame:#1a1a1a;
  --brand-grey:#707070;
  --divider:#9a9a9a;
}
*{box-sizing:border-box;margin:0;padding:0}
html,body{width:1200px;height:849px;overflow:hidden;background:#fff}
body{font-family:'Montserrat',sans-serif;color:var(--ink);position:relative}
.page{position:absolute;top:0;height:849px;background:var(--paper);border:1px solid var(--frame);overflow:hidden}
.page--inside{left:0;width:600px}
.page--cover{left:600px;width:600px}

.brand{position:absolute;display:flex;align-items:center;gap:8px;color:var(--navy);font-weight:400}
.brand__dot{border-radius:50%;background:var(--brand-grey);flex:none}
.page--inside .brand{left:22px;top:88px;font-size:15px;line-height:17px}
.page--inside .brand__dot{width:22px;height:22px}
.page--cover .brand{left:190px;top:150px;font-size:22px;line-height:24px}
.page--cover .brand__dot{width:34px;height:34px}

.text{font-size:7.1px;line-height:9.1px;font-weight:300;text-align:justify;hyphens:auto;-webkit-hyphens:auto;word-spacing:-0.3px}

.consent{position:absolute;left:20px;top:160px;width:177px}
.consent__title{font-weight:700;color:var(--navy);font-size:7.6px;line-height:9px;margin-bottom:11px}
.field{display:flex;align-items:flex-end;gap:3px;margin-bottom:9.2px;white-space:nowrap;font-size:7.3px;line-height:9.1px;font-weight:300}
.field__line{flex:1;border-bottom:0.6px solid var(--ink);height:7px}
.consent__para{margin-bottom:10px;font-size:7.3px}
.field--blank{margin:0 0 14px}

.section{position:absolute;left:211px;width:369px}
.section__head{position:relative;height:20px;margin-bottom:8px}
.section__head::before{content:"";position:absolute;left:0;right:0;top:10px;border-top:0.8px solid var(--rule)}
.section__pill{position:absolute;left:50%;transform:translateX(-50%);top:0;height:20px;padding:0 9px;border-radius:10px;background:var(--navy);color:#fff;font-weight:700;font-size:11px;line-height:20px;letter-spacing:.6px;white-space:nowrap}
.section p{text-align-last:center}
.section--intro{top:28px}
.section--benefits{top:155px}
.section--benefits p{text-align-last:left}
.section--risks{top:254px}

.risk-col{position:absolute;top:343px;width:178px}
.risk-col--1{left:20px}
.risk-col--2{left:211px}
.risk-col--3{left:402px}
.divider{position:absolute;top:345px;height:478px;border-left:0.6px solid var(--divider)}
.risk{margin-bottom:8px}
.risk h3{font-size:7.5px;font-weight:700;color:var(--navy);line-height:9.1px;text-align:left}

.photo-strip{position:absolute;left:0;top:278px;width:600px;height:250px}
.cover-title{position:absolute;left:0;width:600px;top:582px;text-align:center;color:var(--navy);font-size:14px;font-weight:500;letter-spacing:2.4px}
</style>
</head>
<body>

<section class="page page--inside">
  <div class="brand"><span class="brand__dot"></span><span>KEV Orthodontic<br>Society</span></div>

  <div class="consent">
    <h2 class="consent__title">CONSENT TO TREATMENT</h2>
    <div class="field">I hereby authorize <span class="field__line"></span></div>
    <p class="consent__para text">To carry out orthodontic treatment and any other related procedures deemed necessary including X-rays, for the welfare and treatment of:</p>
    <div class="field field--blank"><span class="field__line"></span></div>
    <div class="field">Signature of patient or parent/guardian: <span class="field__line"></span></div>
    <div class="field">Name <span class="field__line"></span></div>
    <div class="field">Relationship to patient <span class="field__line"></span></div>
    <div class="field">Date <span class="field__line"></span> / <span class="field__line"></span> / <span class="field__line"></span></div>
  </div>

  <div class="section section--intro">
    <div class="section__head"><span class="section__pill">ORTHODONTIC TREATMENT</span></div>
    <p class="text">Orthodontic treatment promotes a healthy smile, healthier teeth and gums and a better bite for normal chewing. Orthodontic treatment depends for much of its success on the understanding and co-operation of the patient. This form covers the usual material risks associated with Orthodontic treatment. You may ask your orthodontist to explain anything you do not understand. While recognizing he benefits of healthy teeth and a pleasing smile, you should also be aware that orthodontic treatment has limitations and potential risks and there may be alternative treatment options. You should clarify what is expected of you as a patient, or as the parent of a young patient, to achieve excellent results. Keep in mind that with orthodontic treatment, like other healing arts, results cannot be guaranteed. The unknown factor in any orthodontic correction is the response of the patient to the orthodontic treatment. Should you have any questions please ask.</p>
  </div>

  <div class="section section--benefits">
    <div class="section__head"><span class="section__pill">BENEFITS</span></div>
    <p class="text">Orthodontics plays an important role in improving overall oral health and achieving balance and harmony between the face and teeth for a beautiful, healthy smile, which may enhance one's self esteem. The correct bite of teeth with health muscles and jaw joints will provide optimal chewing function. Properly aligned teeth are easier to brush and so the tendancy to decay may be decreased, as may the likelihood of developing disease of the gums and supporting bone Correctly aligned teeth are less likely to experience abnormal wear. Because of the individual conditions present and the limitations of treatment imposed by the nature each specific benefit may not be attainable for every patient.</p>
  </div>

  <div class="section section--risks">
    <div class="section__head"><span class="section__pill">RISKS</span></div>
    <p class="text">All forms of medical and dental treatment including orthodontics, have some risk and limitations. Fortunately in orthodontics complications are infrequent and when they do occur they are usually of only minor consequence. Nevertheless, they should be considered when making the decision to undergo orthodontic treatment. The principal risks in orthodontic treatment pertain to:</p>
  </div>

  <span class="divider" style="left:204px"></span>
  <span class="divider" style="left:396px"></span>

  <div class="risk-col risk-col--1 text">
    <div class="risk"><h3>1. Oral Hygiene</h3>Orthodontic appliances do not cause tooth decay. Gum disease, tooth decay and permanent markings (decalcification) on teeth can occur if orthodontic patients eat food containing excessive sugar or do not brush teeth frequently or properly. These same problems can occur without orthodontic treatment but the risk is greater to an individual wearing braces. It is imperative during orthodontic treatment that extra care be taken with oral hygiene and tooth brushing in particular.</div>
    <div class="risk"><h3>2. Relapse</h3>Teeth may have a tendency to change their positions after treatment. The long term faithful wearing of retainers should reduce this tendency. Teeth can however, move at any time, whether or not they have had orthodontic treatment. This is especially true during the late teen period when active growth of the facial bones is coming to an end. The most vulnerable teeth are those at the front. Throughout life, the bite can change adversely from various causes such as: eruption of wisdom teeth, growth or maturational changes, mouth breathing, playing of musical instruments and other oral habits. Very occasionally tooth movement will be severe enough to merit a further short course of treatment to ensure a satisfactory result.</div>
    <div class="risk"><h3>3. Periodontal Health</h3>The health of the bone and gums which support the teeth may be affected by orthodontic tooth movement if a condition already exists, and in some rare cases where a condition does not appear to exist. In general, orthodontic treatment lessens the possibility of tooth loss or gums infection due to misalignment of the teeth or jaws. Inflammation of the gums and loss of supporting bone can occur if bacterial plaque is not removed daily with good oral hygiene.</div>
    <div class="risk"><h3>4. Root Shortening</h3>In some patients the length of the roots of the teeth may be shortened during orthodontic treatment. Some patients are prone to this happening, some are not. It is nearly impossible to predict susceptibility. Usually this shortening does not have significant consequences, but on very rare occasions it may become a threat to the longevity of the teeth involved.</div>
  </div>

  <div class="risk-col risk-col--2 text">
    <div class="risk"><h3>5. Jaw Joints</h3>Occasionally patients may suffer pain or dysfunction in the jaw joints (T.M.J's). This may present as joint pain, headaches or ear problems. These problems may occur with or without orthodontic treatment. Any of the above noted symptoms should be reported to the orthodontist. Some patients are susceptible to T.M.J. problems and some are not. Numerous studies have shown that movement of the teeth during orthodontic treatment is unrelated to the onset of T.M.J problems. Just as for painful conditions in other joints discomfort in T.M.J's can last from a few days to several weeks or longe.</div>
    <div class="risk"><h3>6. Tooth Vitality</h3>Sometimes a tooth may have been traumatized by a previous accident or a tooth may be decayed or have large fillings which can cause damage to the nerve of the tooth. Orthodontic tooth movement in some cases aggravates this condition and in rare instances may lead to loss of tooth vitality and discolouration of the tooth requiring root canal treatment and other dental treatment to restore the colour of the tooth.</div>
    <div class="risk"><h3>7. Loose appliances and discomfort</h3>The gums, cheeks or lips may be scratched or irritated by newly placed appliances or by loose or broken appliances or by blows to the mouth. You will be given instruction or minimising these effects. Very rarely loose orthodontic appliances may be accidentally swallowed or aspirated. You should inform your orthodontist of any unusual symptoms, broken or loose appliances, as soon as they are noted. Usual post adjustment tenderness should be expected, and the period of tenderness or sensitivity varies with each patient and the procedure performed. (typical post adjustment tenderness may last 24 to 48 hours.)</div>
    <div class="risk"><h3>8. Atypical Growth</h3>Insufficient, excessive or asymmetrical changes in the growth of the jaws may limit our ability to achieve the desired result. If growth becomes disproportionate during orthodontic management the treatment may be prolonged. Growth changes that occur after orthodontic treatment may alter the quality of treatment results and may require further orthodontic treatment. In some cases of atypical growth, the bite may change so much that oral surgery is required to achieve the best possible result.</div>
  </div>

  <div class="risk-col risk-col--3 text">
    <div class="risk"><h3>9. Headgear</h3>If improperly handled, headgear may cause injury to the face. Patients are warned not to wear the appliance during the times of boisterous or competitive activity.</div>
    <div class="risk"><h3>10. Treatment Time</h3>The total time required to complete treatment may exceed the estimate. Poor co-operation in wearing the appliance or elastics the required hours per day, poor oral hygiene, broken appliances and missed appointments can lengthen the treatment time and affect the quality of the results.</div>
    <div class="risk"><h3>11. Co-operation</h3>Co-operation throughout treatment is your best guarantee of achieving a pleasing smile and good bite. Failure to co-operate could force the orthodontist to change the procedures and goals of your treatment. As a last resort treatment might have to be suspended. The consequences of early suspension may be worse than no treatment at all.</div>
    <div class="risk"><h3>12. Ceramic Brackets</h3>Where ceramic brackets have been used, there have been some reported incidents of patients experiencing bracket breakage or damage to teeth, including the wearing down of tooth enamel and flaking or fracturing of the tooth's enamel on debanding. Fractured brackets may result in remnants which may be harmful to the patient especially if they are chewed on, swallowed or aspirated.</div>
    <div class="risk"><h3>13. Complementary aesthetic dentistry</h3>If your teeth vary from normal in the number, size or shape of the teeth, achievement of the ideal result (for example, complete closure of excessive space) may require restorative treatment. The most common types of complementary treatment are cosmetic bonding, crown and bridge restorative dental care and periodontal therapy.</div>
    <div class="risk"><h3>14. General Health</h3>General medical problems can affect orthodontic treatment. You should keep your orthodontist informed of any changes to you medical health.</div>
  </div>
</section>

<section class="page page--cover">
  <div class="brand"><span class="brand__dot"></span><span>KEV Orthodontic<br>Society</span></div>

  <svg class="photo-strip" viewBox="0 0 600 250" role="img" aria-label="Three angled photo panels: a patient with braces being examined, an orthodontist treating a patient, and a close-up of a bright smile">
    <defs>
      <linearGradient id="tone-patient" x1="0" y1="0" x2="1" y2="1"><stop offset="0" stop-color="#c98f6e"/><stop offset="1" stop-color="#e8d6cc"/></linearGradient>
      <linearGradient id="tone-clinic" x1="0" y1="0" x2="1" y2="1"><stop offset="0" stop-color="#eeeae6"/><stop offset="0.6" stop-color="#c8d8e6"/><stop offset="1" stop-color="#5ea3dc"/></linearGradient>
      <linearGradient id="tone-smile" x1="0" y1="0" x2="0" y2="1"><stop offset="0" stop-color="#f1d2c9"/><stop offset="0.55" stop-color="#d98a94"/><stop offset="1" stop-color="#f0d6cf"/></linearGradient>
    </defs>
    <polygon points="0,1 222,1 171,248 0,248" fill="url(#tone-patient)"/>
    <polygon points="242,1 430,1 383,248 193,248" fill="url(#tone-clinic)"/>
    <polygon points="450,1 600,1 600,248 406,248" fill="url(#tone-smile)"/>
  </svg>

  <h1 class="cover-title">PATIENT CONSENT FORM</h1>
</section>

</body>
</html>
```